We need 3 A2 posters similar look but different enough to be eye catching when changed.

We are a healthcare centre that requires 3 A2 posters - simple, similar but different background colours. These posters will be used within our business to promote services we provide to our clients.

The design should include our logo(attached), a large header and a large section in the middle of the poster to promote the event. We need a blank text box (which WE can insert text to advertise), and 1 image to advertise the event. Please note, we do not need you to choose an image we simply would like you to place a demo to give us an idea of where it should sit.

We want to use the bubble design (attached) as a background and the company colours pink, orange and blue - as on our website. Attached is a copy of our logo and background bubble effect. You can also refer to our website - www.tallowbrookwellness.com.au for more inspiration.

Just to reiterate, these posters should be simple, different but have a uniform feel. They should have an empty middle section that can be edited to add text and a space for an eye catching title and matching image.

Our services include Chiropractic, Podiatry, Nutrition, Massage, Yoga, Pilates and Specialised rehabilitation classes.

Reason: Hi designers, I know we are all busy but I really need more designs from the designers I invited to this project and look forward to receiving more designs. Any questions please let me know. Regards, Marion

Reason: Hi all Increased the budget Regards Marion

Corporate Sydney City office workers

Healthcare

• logo and company colours
section in the middles that can be edited to add text
Space allocated for image placement
Catchy title/header

```html
<!DOCTYPE html>
<html lang="en">
<head>
<meta charset="utf-8">
<title>Tallowbrook Wellness Poster</title>
<link href="https://fonts.googleapis.com/css2?family=Poppins:wght@600&family=Mulish:wght@700&display=swap" rel="stylesheet">
<style>
  :root {
    --brand-blue: #5f82f1;
    --brand-blue-soft: rgba(95, 130, 241, 0.55);
    --brand-magenta: #c233dc;
    --brand-orange: #d98f45;
    --paper: #ffffff;
    --backdrop: #f1f2f4;
    --photo-light: #e6eef5;
    --photo-mid: #b9d2e6;
  }
  * { box-sizing: border-box; margin: 0; padding: 0; }
  html, body {
    width: 903px;
    height: 1200px;
    overflow: hidden;
    background: var(--backdrop);
  }
  .poster {
    position: absolute;
    left: 60px;
    top: 47px;
    width: 782px;
    height: 1106px;
    background: var(--paper);
    overflow: hidden;
  }
  .top-band {
    position: absolute;
    left: 0; top: 0;
    width: 100%;
    height: 76px;
    background: var(--brand-blue);
  }
  .brand {
    position: absolute;
    left: 22px;
    top: 20px;
    display: flex;
    align-items: center;
    gap: 10px;
    font-family: "Mulish", sans-serif;
    font-weight: 700;
    font-size: 30px;
    line-height: 36px;
    color: var(--paper);
  }
  .brand-mark {
    width: 22px;
    height: 22px;
    background: var(--brand-magenta);
  }
  .pointer {
    position: absolute;
    left: 240px;
    top: 82px;
  }
  .decor-squares {
    position: absolute;
    left: 540px;
    top: 86px;
  }
  .headline {
    position: absolute;
    left: 22px;
    top: 166px;
    font-family: "Poppins", sans-serif;
    font-weight: 600;
    font-size: 88px;
    line-height: 72px;
    letter-spacing: -0.5px;
    color: var(--brand-blue);
  }
  .content-box {
    position: absolute;
    left: 57px;
    top: 415px;
    width: 669px;
    height: 646px;
    border: 6px solid var(--brand-blue);
    border-radius: 20px;
    background: var(--paper);
    box-shadow: 0 10px 28px rgba(40, 110, 150, 0.18);
  }
  .feature-photo {
    position: absolute;
    left: 216px;
    top: 349px;
    width: 538px;
    height: 253px;
    border: 4px solid var(--brand-blue);
    border-radius: 12px;
    background: linear-gradient(120deg, var(--photo-mid) 0%, var(--photo-light) 55%, #f4f6f2 100%);
    box-shadow: 0 14px 26px rgba(40, 110, 150, 0.25);
  }
  .intro-copy {
    position: absolute;
    left: 86px;
    top: 682px;
    width: 600px;
    font-family: "Mulish", sans-serif;
    font-weight: 700;
    font-size: 20px;
    line-height: 28px;
    color: var(--brand-blue);
  }
  .intro-copy p + p { margin-top: 28px; }
  .bottom-band {
    position: absolute;
    left: 0;
    bottom: 0;
    width: 100%;
    height: 19px;
    display: flex;
  }
  .bottom-band .band-blue { width: 541px; background: var(--brand-blue); }
  .bottom-band .band-orange { width: 73px; background: var(--brand-orange); }
  .bottom-band .band-magenta { flex: 1; background: var(--brand-magenta); }
</style>
</head>
<body>
  <main class="poster">
    <header class="top-band">
      <div class="brand"><span class="brand-mark"></span>Tallowbrook Wellness</div>
    </header>

    <svg class="pointer" width="72" height="60" viewBox="0 0 72 60" aria-hidden="true">
      <polygon points="0,0 72,0 36,60" fill="var(--brand-blue)"/>
    </svg>

    <svg class="decor-squares" width="230" height="200" viewBox="0 0 230 200" aria-hidden="true">
      <rect x="1" y="84" width="102" height="72" rx="4" fill="var(--brand-blue-soft)"/>
      <rect x="43" y="59" width="93" height="65" rx="4" fill="var(--brand-blue-soft)"/>
      <rect x="44" y="109" width="127" height="89" rx="4" fill="var(--brand-blue-soft)"/>
      <rect x="101" y="20" width="71" height="51" rx="4" fill="var(--brand-blue-soft)"/>
      <rect x="131" y="37" width="88" height="63" rx="4" fill="var(--brand-blue-soft)"/>
      <rect x="130" y="2" width="65" height="46" rx="4" fill="var(--brand-blue-soft)"/>
    </svg>

    <h1 class="headline">Header text<br>space</h1>

    <section class="content-box"></section>

    <div class="feature-photo" role="img" aria-label="Photo placeholder: a family preparing fresh vegetables together in a bright kitchen"></div>

    <div class="intro-copy">
      <p>Welcome to Tallowbrook Wellness. Our goal is to achieve the best possible health outcome for our patients. Our unique combination of therapies, structural correction and individualised exercise programs is what sets us apart.</p>
      <p>At anytime, if you have a health condition, even if you feel it is not something we could help you with, contact us and we will find the right solution for you. We are here for the health of our community"</p>
    </div>

    <footer class="bottom-band">
      <span class="band-blue"></span>
      <span class="band-orange"></span>
      <span class="band-magenta"></span>
    </footer>
  </main>
</body>
</html>
```